Larchmont Claims Collective Business card

We need to get business card Design for our Company we are Public Adjusters in Chicago Illinois - i like to see good combination and elements from my Company Logo. as well To be an two side design
Updates

Target Market(s)

Home /Business owner Property Managers

Industry/Entity Type

Business

Contact Information for Business Card

to show the Element of our logo i will Like 3D

Font styles to use
Sans Serif

Requirements
Must have
• Logo and Element of the Logo in 3D
Nice to have
• Logo That we Provide 3D Same Colors or open for suggestions
Should not have
• unleare view -

```html
<!DOCTYPE html>
<html lang="en">
<head>
<meta charset="utf-8">
<title>Larchmont Claims Collective — Business Card</title>
<link rel="stylesheet" href="https://fonts.googleapis.com/css2?family=Roboto:wght@400;500;700&display=swap">
<style>
  :root {
    --page-bg: #e6e6e6;
    --card-white: #ffffff;
    --brand-blue: #1a2fb0;
    --brand-navy: #0d1f7a;
    --brand-orange: #e05a3c;
    --text-gray: #555a60;
    --rule-blue: #3a4a9a;
  }
  * { margin: 0; padding: 0; box-sizing: border-box; }
  html, body {
    width: 1105px; height: 1200px; overflow: hidden;
    background: var(--page-bg);
    font-family: "Roboto", Arial, sans-serif;
  }
  .canvas { position: relative; width: 1105px; height: 1200px; }

  .card { position: absolute; left: 196px; width: 720px; height: 414px; overflow: hidden; }
  .card-front { top: 145px; background: var(--card-white); }
  .card-back { top: 602px; height: 410px; background: var(--brand-orange); }

  .brand-name {
    position: absolute; right: 36px; top: 62px;
    display: flex; align-items: center; gap: 12px;
    color: var(--brand-blue); font-weight: 700; font-size: 22px; line-height: 1;
  }
  .brand-dot { width: 16px; height: 16px; border-radius: 50%; background: var(--brand-blue); flex: none; }

  .person-name {
    position: absolute; left: 36px; top: 152px;
    color: var(--brand-blue); font-size: 27px; font-weight: 500; line-height: 1.2;
  }
  .person-title {
    position: absolute; left: 36px; top: 186px;
    color: var(--brand-orange); font-size: 20px; line-height: 1.2;
  }
  .rule { position: absolute; left: 36px; top: 218px; width: 641px; height: 2px; background: var(--rule-blue); }

  .contact-list { position: absolute; left: 36px; top: 234px; list-style: none; }
  .contact-list li {
    display: flex; align-items: center; gap: 8px;
    height: 27.5px; color: var(--text-gray); font-size: 18px;
  }
  .contact-list svg { width: 16px; height: 16px; fill: var(--brand-blue); flex: none; }

  .address {
    position: absolute; right: 35px; top: 292px; text-align: right;
    color: var(--text-gray); font-size: 18px; line-height: 25px; font-style: normal;
  }

  .footer-band { position: absolute; left: 0; bottom: 0; width: 720px; height: 48px; }
  .footer-url {
    position: absolute; right: 30px; bottom: 16px;
    color: #ffffff; font-size: 17px; font-weight: 500; letter-spacing: 3.5px;
  }

  .back-brand {
    position: absolute; left: 0; right: 0; top: 140px;
    display: flex; flex-direction: column; align-items: center; gap: 18px;
  }
  .back-circle { width: 74px; height: 74px; border-radius: 50%; background: var(--brand-blue); }
  .back-name { color: var(--brand-blue); font-weight: 700; font-size: 30px; line-height: 1.2; }
  .back-url {
    position: absolute; left: 0; right: 0; top: 347px; text-align: center;
    color: #ffffff; font-size: 17px; letter-spacing: 2.5px;
  }
</style>
</head>
<body>
<main class="canvas">

  <section class="card card-front" aria-label="Business card front">
    <div class="brand-name"><span class="brand-dot"></span>Larchmont Claims Collective</div>

    <h1 class="person-name">MARTIN KELL</h1>
    <p class="person-title">President</p>
    <div class="rule"></div>

    <ul class="contact-list">
      <li><svg viewBox="0 0 16 16" aria-hidden="true"><path d="M1 5c0-2 3-3 7-3s7 1 7 3v1h-4V5H5v1H1z"/><path d="M3 7h10l1 7H2z"/></svg>312 5847 2061</li>
      <li><svg viewBox="0 0 16 16" aria-hidden="true"><path d="M4 0h8a1 1 0 0 1 1 1v14a1 1 0 0 1-1 1H4a1 1 0 0 1-1-1V1a1 1 0 0 1 1-1zm1 2v10h6V2zm3 11a1 1 0 1 0 0 2 1 1 0 0 0 0-2z"/></svg>773 4190 6628</li>
      <li><svg viewBox="0 0 16 16" aria-hidden="true"><path d="M4 1h8v4H4z"/><path d="M1 6h14v6h-2v3H3v-3H1zm4 5v2h6v-2z"/></svg>312 5847 2099</li>
      <li><svg viewBox="0 0 16 16" aria-hidden="true"><path d="M1 3h14v1L8 9 1 4z"/><path d="M1 6l7 5 7-5v7H1z"/></svg>martin@larchmontclaims.com</li>
    </ul>

    <address class="address">4127 Larchmont Avenue<br>Evanston, IL 60201</address>

    <svg class="footer-band" viewBox="0 0 720 48" aria-hidden="true">
      <defs>
        <linearGradient id="bandBlue" x1="0" x2="1" y1="0" y2="0">
          <stop offset="0" stop-color="#1a3ac0"/>
          <stop offset="1" stop-color="#0b1660"/>
        </linearGradient>
      </defs>
      <rect x="0" y="30" width="720" height="18" fill="url(#bandBlue)"/>
      <rect x="0" y="11" width="420" height="19" fill="var(--brand-orange)"/>
      <polygon points="415,0 720,0 720,48 378,48" fill="url(#bandBlue)"/>
    </svg>
    <p class="footer-url">www.larchmontclaims.com</p>
  </section>

  <section class="card card-back" aria-label="Business card back">
    <div class="back-brand">
      <span class="back-circle"></span>
      <span class="back-name">Larchmont Claims Collective</span>
    </div>
    <p class="back-url">www.LarchmontClaimsCollective.com</p>
  </section>

</main>
</body>
</html>
```